Business card for medical clinic

I need an upmarket, modern medical/health business card for my clinic

Contact Information for Business Card

name, address, email, qr code

```html
<!DOCTYPE html>
<html lang="en">
<head>
<meta charset="utf-8">
<title>Meridian Care Clinic – Business Card</title>
<link href="https://fonts.googleapis.com/css2?family=Cinzel:wght@500&family=Arimo:wght@400&display=swap" rel="stylesheet">
<style>
  :root {
    --page-bg: #e6e8ec;
    --card-white: #ffffff;
    --navy: #1b2747;
    --navy-deep: #16203c;
    --sky: #2aa3d9;
    --sky-light: #5cc3ec;
    --text-dark: #3a3d44;
    --text-soft: #5c6069;
    --logo-blue: #1f5f9e;
  }
  * { box-sizing: border-box; margin: 0; padding: 0; }
  html, body { width: 1200px; height: 900px; overflow: hidden; }
  body {
    background: var(--page-bg);
    position: relative;
    font-family: "Arimo", Arial, sans-serif;
  }
  .card {
    position: absolute;
    top: 300px;
    width: 520px;
    height: 300px;
    border-radius: 24px;
    overflow: hidden;
    box-shadow: 0 10px 30px rgba(20, 30, 50, 0.18);
  }
  /* Front side */
  .card--front { left: 60px; background: var(--card-white); }
  .name-band {
    position: absolute;
    left: 0; top: 42px;
    width: 330px; height: 56px;
    background: linear-gradient(90deg, var(--sky) 0%, #1f6fa6 40%, var(--navy) 100%);
  }
  .holder-name {
    position: absolute;
    left: 56px; top: 48px;
    font-family: "Cinzel", "Times New Roman", serif;
    font-weight: 500;
    font-size: 24px;
    letter-spacing: 1px;
    color: var(--card-white);
  }
  .holder-title {
    position: absolute;
    left: 56px; top: 78px;
    font-size: 12px;
    color: #d8ecf7;
  }
  .contact-list {
    position: absolute;
    left: 40px; top: 128px;
    list-style: none;
    font-size: 13px;
    line-height: 20px;
    color: var(--text-dark);
  }
  .contact-list li { display: flex; align-items: center; gap: 7px; }
  .contact-list .address { padding-left: 19px; }
  .contact-list svg { width: 12px; height: 12px; flex: none; }
  .front-logo {
    position: absolute;
    left: 345px; top: 52px;
    display: flex; align-items: center; gap: 8px;
    width: 160px;
  }
  .logo-dot {
    width: 14px; height: 14px; border-radius: 50%;
    background: var(--logo-blue);
    flex: none;
  }
  .logo-name {
    font-family: "Cinzel", "Times New Roman", serif;
    font-weight: 500;
    font-size: 17px;
    line-height: 21px;
    letter-spacing: 1px;
  }
  .front-logo .logo-name { color: var(--logo-blue); }
  /* Back side */
  .card--back {
    left: 620px;
    background: linear-gradient(210deg, var(--navy-deep) 0%, var(--navy) 35%, #1f5f93 65%, var(--sky) 100%);
  }
  .back-logo {
    position: absolute;
    left: 0; right: 0; top: 0; bottom: 0;
    display: flex; align-items: center; justify-content: center; gap: 12px;
  }
  .back-logo .logo-dot { background: var(--card-white); width: 18px; height: 18px; }
  .back-logo .logo-name { color: var(--card-white); font-size: 26px; line-height: 30px; }
</style>
</head>
<body>
  <section class="card card--front" aria-label="Business card front">
    <div class="name-band"></div>
    <h1 class="holder-name">Elena Marsh</h1>
    <p class="holder-title">Director/Founder</p>

    <ul class="contact-list">
      <li class="address">2870 Harbor Lane</li>
      <li class="address">Westfield BR 61830</li>
      <li>
        <svg viewBox="0 0 12 12" aria-hidden="true"><path d="M3 1l2 2-1 1.5c.7 1.4 1.6 2.3 3 3L8.5 6.5l2 2-1.2 1.8C5.5 10 2 6.5 1.5 2.7z" fill="#2aa3d9"/></svg>
        04178 302 7614
      </li>
      <li>
        <svg viewBox="0 0 12 12" aria-hidden="true"><rect x="1" y="2.5" width="10" height="7" rx="1" fill="#2aa3d9"/><path d="M1.5 3l4.5 3.5L10.5 3" stroke="#fff" stroke-width="1" fill="none"/></svg>
        info@meridiancareclinic.com
      </li>
      <li>
        <svg viewBox="0 0 12 12" aria-hidden="true"><circle cx="6" cy="6" r="5" fill="#2aa3d9"/><path d="M1 6h10M6 1c-2 2.5-2 7.5 0 10M6 1c2 2.5 2 7.5 0 10" stroke="#fff" stroke-width="0.8" fill="none"/></svg>
        www.meridiancareclinic.com
      </li>
    </ul>

    <div class="front-logo">
      <span class="logo-dot"></span>
      <span class="logo-name">Meridian Care Clinic</span>
    </div>
  </section>

  <section class="card card--back" aria-label="Business card back">
    <div class="back-logo">
      <span class="logo-dot"></span>
      <span class="logo-name">Meridian Care Clinic</span>
    </div>
  </section>
</body>
</html>
```